CM Candle Tube Packaging Design

Website: www.corvelmare.example
IG: @corvel.mare
Tagline: Elevate Your Ambiance
My brand is a sophisticated brand with luxury candles made of coconut wax. Im looking for an upscale minimalist chic design.
Discover the transformative power of positive energy with Corvel Mare candles. Indulge in true luxury with our specially crafted coconut wax blend that not only ignites captivating scents but also embodies modern elegance and empowering elements.
At Corvel Mare we're committed to delivering a unique and exhilarating aromatic experience to all candle lovers. Each candle is meticulously handcrafted in small batches using luxury fragrance oils exclusively formulated for coconut wax.
Our candles are:
Clean-burning
Paraben-Free
Phthalate-Free
Skin-Safe
Pet-Friendly

```html
<!DOCTYPE html>
<html lang="en">
<head>
<meta charset="UTF-8">
<title>Corvel Mare – Candle Tube Packaging</title>
<link href="https://fonts.googleapis.com/css2?family=Outfit:wght@300;500;600&family=Allura&display=swap" rel="stylesheet">
<style>
  :root {
    --backdrop: #a3b8ab;
    --label-white: #f3f1ef;
    --blush: #e2b6b2;
    --blush-deep: #d8a7a3;
    --ink: #2b2b2b;
    --ink-soft: #4a4a4a;
  }
  * { margin: 0; padding: 0; box-sizing: border-box; }
  html, body { width: 1200px; height: 884px; overflow: hidden; }
  body {
    background: var(--backdrop);
    font-family: "Outfit", sans-serif;
    color: var(--ink);
    position: relative;
  }
  .tube-label {
    position: absolute;
    left: 330px; top: 190px;
    width: 300px; height: 480px;
    background: var(--label-white);
    overflow: hidden;
  }
  .wordmark {
    position: absolute; top: 58px; left: 0; width: 100%;
    text-align: center;
    font-family: "Outfit", sans-serif;
    font-weight: 300;
    font-size: 30px;
    letter-spacing: 1px;
    color: var(--ink);
  }
  .descriptor {
    position: absolute; top: 106px; left: 0; width: 100%;
    display: flex; align-items: center; justify-content: center; gap: 8px;
    font-size: 9.5px; letter-spacing: 3px; color: var(--ink-soft);
  }
  .descriptor .rule { width: 14px; height: 1px; background: var(--ink-soft); }
  .script-line {
    position: absolute; top: 122px; left: 0; width: 100%;
    text-align: center;
    font-family: "Allura", cursive;
    font-size: 14px; color: var(--ink-soft);
  }
  .flame-area {
    position: absolute; left: 70px; top: 194px;
    width: 140px; height: 300px;
    border-radius: 70px 70px 0 0;
    background: linear-gradient(180deg, var(--blush) 0%, var(--blush-deep) 100%);
  }
  .headline {
    position: absolute; left: 95px; top: 268px;
    font-weight: 500; font-size: 18px; line-height: 1.05;
    letter-spacing: 0.8px; color: var(--ink);
  }
  .contact {
    position: absolute; top: 426px; left: 0; width: 100%;
    text-align: center; color: var(--ink);
  }
  .contact .handle {
    display: flex; align-items: center; justify-content: center; gap: 4px;
    font-size: 8px; letter-spacing: 0.6px;
  }
  .contact .handle .dot {
    width: 9px; height: 9px; border: 1px solid var(--ink); border-radius: 2px;
  }
  .contact .site {
    margin-top: 5px; font-size: 8.5px; font-weight: 600; letter-spacing: 1.2px;
  }
  .lid {
    position: absolute; left: 690px; top: 420px;
    width: 230px; height: 230px; border-radius: 50%;
    background: var(--blush);
    border: 5px solid var(--label-white);
    display: flex; align-items: center; justify-content: center;
  }
  .lid .monogram {
    font-family: "Outfit", sans-serif; font-weight: 300;
    font-size: 38px; letter-spacing: 2px; color: var(--ink);
  }
</style>
</head>
<body>
  <section class="tube-label">
    <h1 class="wordmark">CORVEL MARE</h1>
    <div class="descriptor"><span class="rule"></span>HANDMADE CANDLES<span class="rule"></span></div>
    <p class="script-line">with purpose and love</p>
    <div class="flame-area" role="img" aria-label="Large soft pink flame motif"></div>
    <h2 class="headline">Elevate Your<br>Ambiance</h2>
    <div class="contact">
      <div class="handle"><span class="dot"></span>@corvel.mare</div>
      <div class="site">www.corvelmare.example</div>
    </div>
  </section>
  <div class="lid">
    <span class="monogram">CM</span>
  </div>
</body>
</html>
```